Business cards to launch an education platform

Hi,
I am looking at having new business cards designed.
I am a startup, developing a web platform for schools and university, the education world. It's an online assessment system.
I would like a card that looks classy, and that is using the colors and the font of my logo.

I have attached:
1) my logo
2) A business card that I have designed quickly so you can have all the information required in the card, but I really don't like it.
3) The font that I am using (Lato Regular) to design my web platform
4) Some screenshots of my web platform so you can have a look at the style that I have.

Target Market(s)

Major market: Education system: Schools and university
Minor markets: Business in general

Industry/Entity Type

Business

Contact Information for Business Card

Clara Fenwick
Director

M: 0437 518 902
E: clara.fenwick@amberLoomSystems.com.au

Requirements
Must have
• The colors of my logo

```html
<!DOCTYPE html>
<html lang="en">
<head>
<meta charset="utf-8">
<title>Amber Loom Systems – Business Card</title>
<link href="https://fonts.googleapis.com/css2?family=Lato:wght@400;700&family=Roboto+Condensed:wght@400;500&family=Roboto:wght@400&display=swap" rel="stylesheet">
<style>
  :root {
    --stage: #9c9d9f;
    --paper: #eceef1;
    --navy: #0b3a6d;
    --navy-deep: #08305c;
    --sky: #27a2d9;
    --sky-text: #2ba6de;
    --white: #ffffff;
    --back-light: #dfe5ee;
    --teal: #1b7fa8;
  }
  * { margin: 0; padding: 0; box-sizing: border-box; }
  html, body {
    width: 1105px;
    height: 1200px;
    overflow: hidden;
    background: var(--stage);
  }
  .card {
    position: absolute;
    left: 182px;
    width: 746px;
    height: 425px;
    overflow: hidden;
  }
  .card--front { top: 119px; background: var(--paper); }
  .card--back  { top: 637px; background: var(--navy); }

  .front-bands {
    position: absolute;
    inset: 0;
    width: 100%;
    height: 100%;
  }

  .brand {
    position: absolute;
    left: 46px;
    top: 52px;
    display: flex;
    align-items: center;
    gap: 16px;
  }
  .brand__mark {
    width: 70px;
    height: 70px;
    background: var(--navy);
  }
  .brand__name {
    font-family: 'Lato', sans-serif;
    font-weight: 400;
    color: var(--navy);
    line-height: 1.05;
  }
  .brand__name-main {
    display: block;
    font-size: 36px;
    letter-spacing: 2px;
  }
  .brand__name-sub {
    display: block;
    font-size: 27px;
    letter-spacing: 2px;
  }

  .contact {
    position: absolute;
    right: 76px;
    text-align: right;
  }
  .contact__name {
    top: 240px;
    font-family: 'Roboto Condensed', sans-serif;
    font-weight: 500;
    font-size: 31px;
    color: var(--sky-text);
    letter-spacing: 0.3px;
  }
  .contact__role {
    top: 282px;
    font-family: 'Roboto Condensed', sans-serif;
    font-weight: 500;
    font-size: 21px;
    color: var(--white);
  }
  .contact__line {
    right: 50px;
    font-family: 'Roboto', sans-serif;
    font-size: 19px;
    color: var(--white);
    display: flex;
    align-items: center;
    gap: 12px;
  }
  .contact__line--phone { top: 332px; right: 48px; }
  .contact__line--email { top: 360px; right: 46px; font-size: 18.5px; }
  .contact__icon { flex: none; }

  .back-backdrop {
    position: absolute;
    inset: 0;
    background:
      radial-gradient(ellipse 60% 70% at 78% 80%, rgba(27,127,168,0.9), rgba(27,127,168,0) 70%),
      radial-gradient(ellipse 55% 60% at 22% 55%, rgba(22,84,150,0.7), rgba(22,84,150,0) 70%),
      linear-gradient(135deg, var(--navy-deep) 0%, var(--navy) 50%, #0f4d85 100%);
  }
  .back-brand {
    position: absolute;
    left: 0;
    width: 804px;
    top: 156px;
    text-align: center;
    font-family: 'Lato', sans-serif;
    font-weight: 400;
    color: var(--back-light);
  }
  .back-brand__main {
    display: block;
    font-size: 56px;
    letter-spacing: 6px;
    line-height: 1;
  }
  .back-brand__sub {
    display: block;
    margin-top: 12px;
    font-size: 38px;
    letter-spacing: 4px;
    line-height: 1;
  }
  .back-url {
    position: absolute;
    left: 0;
    width: 804px;
    top: 264px;
    text-align: center;
    font-family: 'Lato', sans-serif;
    font-size: 20px;
    letter-spacing: 1.2px;
    color: var(--back-light);
  }
</style>
</head>
<body>

<section class="card card--front" aria-label="Business card front">
  <svg class="front-bands" viewBox="0 0 540 308" preserveAspectRatio="none" aria-hidden="true">
    <polygon fill="var(--sky)" points="0,222 76,254 520,31 528,31 522,40 76,263 0,232"/>
    <polygon fill="var(--navy)" points="0,240 76,272 540,40 540,308 0,308"/>
  </svg>

  <div class="brand">
    <span class="brand__mark"></span>
    <span class="brand__name">
      <span class="brand__name-main">AMBER LOOM</span>
      <span class="brand__name-sub">Systems</span>
    </span>
  </div>

  <div class="contact contact__name">CLARA FENWICK</div>
  <div class="contact contact__role">DIRECTOR</div>

  <div class="contact contact__line contact__line--phone">
    <span>0437 518 902</span>
    <svg class="contact__icon" width="14" height="22" viewBox="0 0 14 22" aria-hidden="true">
      <rect x="1" y="1" width="12" height="20" rx="2" fill="none" stroke="var(--sky)" stroke-width="2"/>
      <rect x="5" y="17" width="4" height="1.5" fill="var(--sky)"/>
    </svg>
  </div>
  <div class="contact contact__line contact__line--email">
    <span>clara.fenwick@amberLoomSystems.com.au</span>
    <svg class="contact__icon" width="18" height="13" viewBox="0 0 18 13" aria-hidden="true">
      <rect x="0" y="0" width="18" height="13" fill="var(--sky)"/>
      <polyline points="1,1 9,7 17,1" fill="none" stroke="var(--navy)" stroke-width="1.5"/>
    </svg>
  </div>
</section>

<section class="card card--back" aria-label="Business card back">
  <div class="back-backdrop" role="img" aria-label="Soft blue gradient backdrop"></div>
  <div class="back-brand">
    <span class="back-brand__main">AMBER LOOM</span>
    <span class="back-brand__sub">Systems</span>
  </div>
  <div class="back-url">amberLoomSystems.com.au</div>
</section>

</body>
</html>
```